KRT Engineering Business Card Design

We’re looking for an elegant, clean, and timeless business card design that communicates experience, capability, and reliability.

KRT Engineering was established in 1995 , we are a Government Contracting company providing Professional Services to the Office of Frontier Affairs, Harbor Protection and the Vantage Collective. Our capabilities include: Acquisition & Program Management; Intelligence & Security Operations; Cyber, IT & Network Operations; Lifecycle Logistics & Asset Readiness; C5ISR Systems Engineering & Sustainment.

We want the card to reflect a straightforward, confident approach to business. The design should feel polished and professional without being flashy or overly corporate.

Design Direction
Clean, sophisticated, and uncluttered
Elegant but understated
Strong typography and thoughtful spacing
A timeless aesthetic rather than something overly trendy
Confident and established, with a sense of substance
Easy to read and practical in a real-world business setting

The overall impression should be: “These are experienced professionals who know what they’re doing, do what they say, and can be relied upon.”

We’re open to creative interpretations. The finished card should feel distinctive through its typography, proportions, layout, and attention to detail rather than through excessive graphics or visual effects.

We’re looking for a design that would make a potential client immediately feel that they’re dealing with a capable, trustworthy, and established company.

Company Colors: Navy and Gold/Yellow (but you do not need to use these colors on the card)
Company Name: KRT Engineering Associates, Inc. (known as KRT Engineering)
Website: krtengineering.com
Company Logo: Navy & Gold (other variations attached)

```html
<!DOCTYPE html>
<html lang="en">
<head>
<meta charset="utf-8">
<title>KRT Engineering Business Card</title>
<link href="https://fonts.googleapis.com/css2?family=Manrope:wght@500;600;700;800&family=Barlow:wght@500;600&display=swap" rel="stylesheet">
<style>
  :root {
    --navy: #1b2742;
    --navy-ink: #1f2a5c;
    --gold: #c9a13b;
    --slate: #5d6a92;
    --paper: #efefef;
    --stage: #d3d3d3;
    --white: #ffffff;
    --ink: #15181f;
  }
  * { margin: 0; padding: 0; box-sizing: border-box; }
  html, body { width: 1200px; height: 1200px; overflow: hidden; }
  body { background: var(--stage); font-family: "Manrope", sans-serif; position: relative; }

  .card { position: absolute; left: 180px; width: 840px; height: 480px; background: var(--paper); overflow: hidden; }
  .card--front { top: 78px; }
  .card--back { top: 630px; }

  /* Front */
  .front__brand-panel { position: absolute; left: 0; top: 0; width: 377px; height: 480px; background: var(--navy); }
  .wordmark { font-family: "Manrope", sans-serif; font-weight: 800; letter-spacing: -0.02em; line-height: 1; }
  .front__wordmark { position: absolute; left: 108px; top: 112px; font-size: 78px; color: var(--white); }
  .front__company { position: absolute; left: 68px; top: 274px; font-size: 16px; font-weight: 600; letter-spacing: 0.32em; line-height: 20px; color: var(--slate); }
  .front__established { position: absolute; left: 68px; top: 377px; font-size: 16px; font-weight: 700; letter-spacing: 0.08em; line-height: 20px; color: var(--slate); }
  .front__established span { color: var(--gold); }
  .front__rule { position: absolute; left: 195px; top: 387px; width: 583px; height: 1px; background: var(--gold); }

  .person__name { position: absolute; left: 431px; top: 78px; font-size: 37px; font-weight: 800; color: var(--navy-ink); letter-spacing: -0.01em; }
  .person__title { position: absolute; left: 431px; top: 126px; font-size: 19px; font-weight: 600; color: var(--gold); }
  .person__rule { position: absolute; left: 431px; top: 163px; width: 347px; height: 1px; background: var(--gold); }

  .contact { position: absolute; left: 431px; display: flex; align-items: flex-start; gap: 16px; font-size: 21px; font-weight: 500; color: var(--ink); line-height: 26px; }
  .contact svg { flex: none; width: 24px; height: 24px; margin-top: 1px; }
  .contact--phone { top: 191px; }
  .contact--address { top: 235px; }
  .contact--web { top: 331px; }

  .front__tagline { position: absolute; left: 431px; top: 399px; font-size: 16px; font-weight: 700; letter-spacing: 0.12em; color: var(--navy-ink); }

  /* Back */
  .back__wordmark { position: absolute; left: 0; width: 840px; top: 62px; text-align: center; font-size: 100px; color: var(--navy-ink); }
  .back__company { position: absolute; left: 0; width: 840px; top: 177px; text-align: center; font-size: 13px; font-weight: 600; letter-spacing: 0.32em; color: var(--navy-ink); }
  .back__established { position: absolute; left: 158px; width: 524px; top: 209px; display: flex; align-items: center; gap: 10px; font-size: 13px; font-weight: 600; letter-spacing: 0.3em; color: var(--navy-ink); white-space: nowrap; }
  .back__established::before, .back__established::after { content: ""; flex: 1; height: 1px; background: var(--gold); }
  .back__services-line { position: absolute; left: 0; width: 840px; top: 238px; text-align: center; font-size: 13px; font-weight: 500; letter-spacing: 0.24em; color: var(--navy-ink); }

  .capabilities { position: absolute; left: 0; top: 275px; width: 840px; height: 205px; background: var(--navy); }
  .capability { position: absolute; top: 32px; width: 150px; margin-left: -75px; text-align: center; }
  .capability__icon { display: block; width: 60px; height: 60px; margin: 0 auto; border: 1.5px solid var(--gold); border-radius: 6px; opacity: 0.85; }
  .capability__label { margin-top: 17px; font-family: "Barlow", sans-serif; font-weight: 500; font-size: 13.5px; line-height: 16.5px; color: var(--white); text-transform: uppercase; }
  .capability__rule { width: 82px; height: 1px; margin: 9px auto 0; background: var(--gold); }
</style>
</head>
<body>

<section class="card card--front">
  <div class="front__brand-panel">
    <div class="wordmark front__wordmark">KRT</div>
    <div class="front__company">KRT ENGINEERING<br>ASSOCIATES, INC.</div>
    <div class="front__established">ESTABLISHED<br><span>IN 1995</span></div>
  </div>
  <div class="front__rule"></div>

  <div class="person__name">Marian Holloway</div>
  <div class="person__title">President, CEO &amp; Founder</div>
  <div class="person__rule"></div>

  <div class="contact contact--phone">
    <svg viewBox="0 0 24 24" fill="none" stroke="#c9a13b" stroke-width="1.8" stroke-linejoin="round"><path d="M5 3h4l2 5-2.5 1.5a11 11 0 0 0 6 6L16 13l5 2v4a2 2 0 0 1-2 2A17 17 0 0 1 3 5a2 2 0 0 1 2-2z"/></svg>
    <span>757-555-0148</span>
  </div>
  <div class="contact contact--address">
    <svg viewBox="0 0 24 24" fill="none" stroke="#c9a13b" stroke-width="1.5"><path d="M4 21V4h9v17M13 9h7v12M2 21h20M7 8h3M7 12h3M7 16h3M16 13h2M16 17h2"/></svg>
    <span>4820 Harbor Ridge Road,<br>Suite 310, Norfolk,<br>VA 23510</span>
  </div>
  <div class="contact contact--web">
    <svg viewBox="0 0 24 24" fill="none" stroke="#c9a13b" stroke-width="1.5"><circle cx="12" cy="12" r="9"/><ellipse cx="12" cy="12" rx="4" ry="9"/><path d="M3 12h18M5 7h14M5 17h14"/></svg>
    <span>krtengineering.com</span>
  </div>

  <div class="front__tagline">EXPERIENCE. CAPABILITY. RELIABILITY.</div>
</section>

<section class="card card--back">
  <div class="wordmark back__wordmark">KRT</div>
  <div class="back__company">KRT ENGINEERING ASSOCIATES, INC.</div>
  <div class="back__established">ESTABLISHED 1995</div>
  <div class="back__services-line">Professional Services for Defense, Security &amp; Intelligence</div>

  <div class="capabilities">
    <div class="capability" style="left:111px">
      <span class="capability__icon" role="img" aria-label="Line icon of a handshake above a team"></span>
      <div class="capability__label">Acquisition &amp;<br>Program<br>Management</div>
      <div class="capability__rule"></div>
    </div>
    <div class="capability" style="left:264px">
      <span class="capability__icon" role="img" aria-label="Line icon of a shield with a padlock"></span>
      <div class="capability__label">Intelligence<br>&amp; Security<br>Operations</div>
      <div class="capability__rule"></div>
    </div>
    <div class="capability" style="left:420px">
      <span class="capability__icon" role="img" aria-label="Line icon of a monitor with a cloud network"></span>
      <div class="capability__label">Cyber, IT &amp;<br>Network<br>Operations</div>
      <div class="capability__rule"></div>
    </div>
    <div class="capability" style="left:571px">
      <span class="capability__icon" role="img" aria-label="Line icon of a globe and delivery truck"></span>
      <div class="capability__label">Lifecycle<br>Logistics &amp; Asset<br>Readiness</div>
      <div class="capability__rule"></div>
    </div>
    <div class="capability" style="left:731px">
      <span class="capability__icon" role="img" aria-label="Line icon of a satellite dish"></span>
      <div class="capability__label">C5ISR Systems<br>Engineering &amp;<br>Sustainment</div>
      <div class="capability__rule"></div>
    </div>
  </div>
</section>

</body>
</html>
```